Business card design for my company.
I would like the card's background colour to be black. You can also see our web site to get an idea of our brand. https://www.tmwhomecrafting.com.au/
- Name
- Email

```html
<!DOCTYPE html>
<html lang="en">
<head>
<meta charset="utf-8">
<title>TMW Home Crafting – Business Card</title>
<link href="https://fonts.googleapis.com/css2?family=Montserrat:wght@400;500;700&display=swap" rel="stylesheet">
<style>
  :root {
    --stage: #1c1c1c;
    --card-black: #1f1f1f;
    --card-green: #0c9648;
    --ink-light: #ffffff;
    --ink-grey: #9a9a9a;
    --accent-green: #1a9a4a;
  }
  * { box-sizing: border-box; margin: 0; padding: 0; }
  html, body {
    width: 1200px; height: 875px; overflow: hidden;
    background: var(--stage);
    font-family: "Montserrat", sans-serif;
  }
  .canvas {
    width: 1200px; height: 875px;
    display: flex; align-items: center; justify-content: center; gap: 50px;
  }
  .card {
    width: 525px; height: 300px;
    border-radius: 22px;
    position: relative;
    box-shadow: 0 18px 40px rgba(0,0,0,0.5);
  }
  /* Front */
  .card-front {
    background: var(--card-black);
    display: flex; flex-direction: column; align-items: center; justify-content: center; gap: 16px;
  }
  .brand {
    display: flex; align-items: center; gap: 14px;
  }
  .brand-square {
    width: 22px; height: 22px; background: var(--accent-green);
  }
  .brand-name {
    font-weight: 700; font-size: 30px; letter-spacing: 3px;
    color: var(--ink-grey);
  }
  .brand-tagline {
    font-weight: 500; font-size: 13px; letter-spacing: 6px;
    color: var(--ink-grey); text-transform: uppercase;
  }
  /* Back */
  .card-back {
    background: var(--card-green);
    color: var(--ink-light);
    display: flex; align-items: center; padding: 0 34px;
  }
  .person { flex: 0 0 auto; text-align: right; padding-right: 22px; }
  .person-name { font-weight: 700; font-size: 24px; letter-spacing: 0.5px; text-transform: uppercase; }
  .person-role { font-weight: 400; font-size: 14px; margin-top: 2px; }
  .divider { width: 1.5px; height: 90px; background: var(--ink-light); }
  .contacts { list-style: none; padding-left: 20px; display: flex; flex-direction: column; gap: 7px; }
  .contact { display: flex; align-items: center; gap: 9px; font-size: 12.5px; }
  .contact svg { width: 12px; height: 12px; flex: 0 0 12px; fill: var(--ink-light); }
</style>
</head>
<body>
<main class="canvas">
  <section class="card card-front" aria-label="Card front">
    <div class="brand">
      <span class="brand-square"></span>
      <span class="brand-name">TMW</span>
    </div>
    <p class="brand-tagline">Home Crafting</p>
  </section>

  <section class="card card-back" aria-label="Card back">
    <div class="person">
      <h1 class="person-name">Liam Hartley</h1>
      <p class="person-role">General Manager</p>
    </div>
    <span class="divider"></span>
    <ul class="contacts">
      <li class="contact">
        <svg viewBox="0 0 12 12"><path d="M6 0a4 4 0 0 0-4 4c0 3 4 8 4 8s4-5 4-8a4 4 0 0 0-4-4zm0 5.5A1.5 1.5 0 1 1 6 2.5a1.5 1.5 0 0 1 0 3z"/></svg>
        Riverton, Tasmania, Australia
      </li>
      <li class="contact">
        <svg viewBox="0 0 12 12"><path d="M2.5 0.5l2 2.2-1 1.3c.7 1.6 2 2.9 3.5 3.6l1.3-1 2.2 2-1.2 1.9C5 10.2 1.8 7 .6 1.7z"/></svg>
        0400 123 456
      </li>
      <li class="contact">
        <svg viewBox="0 0 12 12"><path d="M0 2h12v8H0zM1 3v.4l5 3.2 5-3.2V3z"/></svg>
        info@tmwhomecrafting.com.au
      </li>
      <li class="contact">
        <svg viewBox="0 0 12 12"><path d="M6 0a6 6 0 1 0 0 12A6 6 0 0 0 6 0zm0 1c.8 1 1.3 2.3 1.4 4.5H4.6C4.7 3.3 5.2 2 6 1zM1 6.5h2.6c.1 1.8.5 3.2 1.1 4.3A5 5 0 0 1 1 6.5zm0-1a5 5 0 0 1 3.7-4.3c-.6 1.1-1 2.5-1.1 4.3zm5 5.5c-.8-1-1.3-2.3-1.4-4.5h2.8C7.3 8.7 6.8 10 6 11zm1.3-.2c.6-1.1 1-2.5 1.1-4.3H11a5 5 0 0 1-3.7 4.3zM8.4 5.5c-.1-1.8-.5-3.2-1.1-4.3A5 5 0 0 1 11 5.5z"/></svg>
        tmwhomecrafting.com.au
      </li>
    </ul>
  </section>
</main>
</body>
</html>
```